Varelko App for Smart Devices IoT WiFi Electronic

Varelko is a siren manufacturer. This application is used for the company's products that have a Wi-Fi connection and an internet connection, which can be configured and activated remotely through this application. In addition, this application is used to activate the siren at specific times for the start and end of shifts in companies and schools. Users will be siren installers and IT or HR managers.
In addition to activating motorized sirens timers, some siren models have speakers and allow you to play TTS (text to speech) audio, audio recorded by the user on the phone and upload audio (mp3) with playlist programming with start and end times.
Application screens: home with dashboard (one dashboard for each category). Device categories: timers, speakers, motorized siren. Screen for requesting evaluation in the Play Store. Screen for registering the user profile. Screen for registering devices according to their category (timers, speakers, motorized siren). Screen for registering device groups. Screen for pairing the device on the client's Wi-Fi network. Screen for registering activation times. Screen for uploading MP3 audios. Screen for registering playlists with audio selection, start and end times. Screen for recording audio for later sending to the speakers. Screen for converting text to speech and sending to the speakers. It is important to have a time picker with the day of the week to program the activation times and playlist.

Target Market(s)

Schools, Companies and Stores.

Industry/Entity Type

IoT

Font styles to use
Sans Serif
Other font styles liked:
• roboto

Colors
FFC000
F8CF3A
FAE287
FDF2CF
FEFAEE

Requirements
Must have
• time picker with weekdays for timer programming feature.
Nice to have
• app review request screen on play store

```html
<!DOCTYPE html>
<html lang="en">
<head>
<meta charset="utf-8">
<title>Varelko – Siren App Screens</title>
<link rel="stylesheet" href="https://fonts.googleapis.com/css2?family=Ubuntu:wght@400;500;700&display=swap">
<style>
:root{
  --brand:#ffc000;
  --brand-2:#f8cf3a;
  --brand-3:#fae287;
  --brand-4:#fdf2cf;
  --accent:#ff8a00;
  --ink:#1d1d1d;
  --muted:#7a7a7a;
  --line:#dcdcdc;
  --card:#ffffff;
  --bg:#ffffff;
  --field:#b9b9b9;
}
*{box-sizing:border-box;margin:0;padding:0}
html,body{width:1200px;height:569px;overflow:hidden;background:var(--bg);font-family:"Ubuntu",sans-serif;color:var(--ink)}
.canvas{position:relative;width:1200px;height:569px}
.screen{position:absolute;top:64px;width:202px;height:435px;background:#fff;border-radius:28px;border:1px solid #e6e6e6;overflow:hidden}
.screen > *{position:absolute}
.s1{left:80px}.s2{left:356px}.s3{left:631px}.s4{left:907px}
.brand-name{left:14px;top:17px;font-size:15px;font-weight:500;color:var(--brand)}
.top-icons{right:14px;top:20px;display:flex;gap:5px}
.top-icons svg{width:11px;height:11px;stroke:var(--ink);fill:none;stroke-width:1.4}
.title{left:0;width:100%;text-align:center;font-size:10px;font-weight:500}
.card{left:13px;width:176px;background:var(--card);border-radius:6px;box-shadow:0 1px 4px rgba(0,0,0,.14)}
.card > *{position:absolute}
.tiny{font-size:5.5px;color:var(--ink)}
.toggle{width:13px;height:7px;border-radius:4px;background:var(--accent)}
.toggle::after{content:"";position:absolute;right:-1px;top:-1px;width:9px;height:9px;border-radius:50%;background:#fff;box-shadow:0 0 2px rgba(0,0,0,.3)}
.toggle.off{background:#e2e2e2}
.toggle.off::after{right:auto;left:-1px}
.ico{width:8px;height:8px;fill:none;stroke:var(--ink);stroke-width:1.2}
.section{left:19px;font-size:9.5px;font-weight:500;display:flex;align-items:center;gap:4px}
.label{left:16px;font-size:6.5px;font-weight:500}
.field{left:14px;width:174px;height:21px;border:1px solid var(--line);border-radius:4px;font-size:7px;color:var(--field);padding:6px 8px}
.btn-add{left:57px;top:383px;width:86px;height:24px;border-radius:12px;background:var(--accent);color:var(--ink);font-size:8px;font-weight:500;text-align:center;line-height:24px}
.device{left:14px;width:174px;height:22px;border:1px solid var(--line);border-radius:4px;font-size:8.5px;padding:5px 10px;display:flex;justify-content:space-between;align-items:center}
.illustration{left:53px;top:116px;width:94px;height:94px;border-radius:50%;background:radial-gradient(circle at 50% 50%,#f4f4f4 0 30%,var(--brand) 31%)}
.pair-mark{left:43px;top:133px;width:114px;height:114px;border-radius:50%;border:14px solid var(--brand);display:flex;align-items:center;justify-content:center;font-size:16px;font-weight:500;color:var(--brand)}
.pair{left:11px;top:277px;width:173px;height:39px;border-radius:20px;box-shadow:0 1px 5px rgba(0,0,0,.15)}
.pair > *{position:absolute}
</style>
</head>
<body>
<div class="canvas">

<!-- Screen 1: Timers dashboard -->
<section class="screen s1">
  <div class="brand-name">Varelko</div>
  <div class="top-icons">
    <svg viewBox="0 0 12 12"><path d="M1 5a7 7 0 0 1 10 0M3 7a4 4 0 0 1 6 0"/><circle cx="6" cy="9.5" r=".8" fill="#1d1d1d"/></svg>
    <svg viewBox="0 0 12 12"><rect x="1" y="1" width="4" height="4"/><rect x="7" y="1" width="4" height="4"/><rect x="1" y="7" width="4" height="4"/><rect x="7" y="7" width="4" height="4"/></svg>
    <svg viewBox="0 0 12 12"><circle cx="6" cy="6" r="5"/><circle cx="6" cy="5" r="1.8"/><path d="M3 9.5a4 3 0 0 1 6 0"/></svg>
  </div>
  <div class="title" style="top:56px">Motorized Screens Timers</div>
  <div class="card" style="top:75px;height:40px">
    <div style="left:8px;top:9px;font-size:7.5px;font-weight:500">Shift Timing</div>
    <div style="left:8px;top:24px;font-size:7px;color:#555">Activate the device for shift timing</div>
    <div class="toggle" style="right:12px;top:9px"></div>
  </div>
  <div class="section" style="top:136px">
    <svg class="ico" viewBox="0 0 10 10" style="stroke:var(--accent)"><rect x="1" y="2" width="8" height="7"/><path d="M1 4h8M3 1v2M7 1v2"/></svg>Schedules</div>

  <div class="card" style="top:151px;height:54px">
    <div class="tiny" style="left:8px;top:6px">9:00 AM to 1:00 PM</div>
    <div class="tiny" style="left:100px;top:6px">Weekdays</div>
    <div class="tiny" style="left:8px;top:24px">1st half session</div>
    <div class="tiny" style="left:8px;top:41px"><span style="color:var(--accent)">Audio:</span> text to speech</div>
    <div class="tiny" style="left:8px;top:50px;top:49px">The shift has been started, Have a nice day</div>
    <svg class="ico" viewBox="0 0 10 10" style="right:8px;top:6px"><circle cx="5" cy="5" r="4"/><path d="M5 2.5V5l1.5 1"/></svg>
    <svg class="ico" viewBox="0 0 10 10" style="right:8px;top:22px"><path d="M1 9l1-3 5-5 2 2-5 5z"/></svg>
  </div>
  <div class="card" style="top:212px;height:32px">
    <div class="tiny" style="left:8px;top:6px">1:00 PM to 2:00 PM</div>
    <div class="tiny" style="left:100px;top:6px">Weekdays</div>
    <div class="tiny" style="left:6px;top:21px">Lunch Time</div>
    <svg class="ico" viewBox="0 0 10 10" style="right:8px;top:5px"><circle cx="5" cy="5" r="4"/><path d="M5 2.5V5l1.5 1"/></svg>
    <svg class="ico" viewBox="0 0 10 10" style="right:8px;top:19px"><path d="M1 9l1-3 5-5 2 2-5 5z"/></svg>
  </div>
  <div class="card" style="top:251px;height:33px">
    <div class="tiny" style="left:8px;top:6px">4:00 PM to 4:20 PM</div>
    <div class="tiny" style="left:100px;top:6px">Weekdays</div>
    <div class="tiny" style="left:6px;top:21px">Coffee Break</div>
    <svg class="ico" viewBox="0 0 10 10" style="right:8px;top:5px"><circle cx="5" cy="5" r="4"/><path d="M5 2.5V5l1.5 1"/></svg>
    <svg class="ico" viewBox="0 0 10 10" style="right:8px;top:19px"><path d="M1 9l1-3 5-5 2 2-5 5z"/></svg>
  </div>
  <div class="card" style="top:290px;height:33px">
    <div class="tiny" style="left:8px;top:6px">6:00 PM</div>
    <div class="tiny" style="left:100px;top:6px">Weekdays</div>
    <div class="tiny" style="left:6px;top:21px">Signing out Time</div>
    <svg class="ico" viewBox="0 0 10 10" style="right:8px;top:5px"><circle cx="5" cy="5" r="4"/><path d="M5 2.5V5l1.5 1"/></svg>
    <svg class="ico" viewBox="0 0 10 10" style="right:8px;top:19px"><path d="M1 9l1-3 5-5 2 2-5 5z"/></svg>
  </div>
  <div class="card" style="top:331px;height:33px">
    <div class="tiny" style="left:8px;top:6px">9:00 AM to 12 PM</div>
    <div class="tiny" style="left:100px;top:6px">Weekdays</div>
    <div class="tiny" style="left:6px;top:21px">Special Session</div>
    <svg class="ico" viewBox="0 0 10 10" style="right:8px;top:5px"><circle cx="5" cy="5" r="4"/><path d="M5 2.5V5l1.5 1"/></svg>
    <svg class="ico" viewBox="0 0 10 10" style="right:8px;top:19px"><path d="M1 9l1-3 5-5 2 2-5 5z"/></svg>
  </div>
  <div class="section" style="top:375px">
    <svg class="ico" viewBox="0 0 10 10"><rect x="1" y="1" width="8" height="8"/><path d="M3 5l1.5 1.5L8 3"/></svg>Status</div>
  <div style="left:19px;top:392px;width:170px;font-size:6.3px;line-height:9px;color:var(--muted)">Next Ring of siren is at 1:00 PM to 2:00 PM which is lunch time (Siren alarm in 20 mins)</div>
</section>

<!-- Screen 2: Add schedule -->
<section class="screen s2">
  <div class="brand-name">Varelko</div>
  <div class="top-icons">
    <svg viewBox="0 0 12 12"><path d="M1 5a7 7 0 0 1 10 0M3 7a4 4 0 0 1 6 0"/><circle cx="6" cy="9.5" r=".8" fill="#1d1d1d"/></svg>
    <svg viewBox="0 0 12 12"><rect x="1" y="1" width="4" height="4"/><rect x="7" y="1" width="4" height="4"/><rect x="1" y="7" width="4" height="4"/><rect x="7" y="7" width="4" height="4"/></svg>
    <svg viewBox="0 0 12 12"><circle cx="6" cy="6" r="5"/><circle cx="6" cy="5" r="1.8"/><path d="M3 9.5a4 3 0 0 1 6 0"/></svg>
  </div>
  <div class="title" style="top:52px">Add the new schedules for siren</div>
  <div class="label" style="top:76px">Title of Siren alarm</div>
  <div class="field" style="top:88px">Enter</div>
  <div class="label" style="top:117px">Start time of siren</div>
  <div class="field" style="top:129px">Time</div>
  <div class="label" style="top:160px">End time of siren</div>
  <div class="field" style="top:172px">Time</div>
  <div class="label" style="top:212px">Week:</div>
  <div class="label" style="top:212px;left:104px">Weekdays</div>
  <div class="label" style="top:212px;left:165px">Weekend</div>
  <div class="toggle" style="left:115px;top:226px"></div>
  <div class="toggle" style="left:174px;top:226px"></div>
  <div class="label" style="top:245px">Audio Format</div>
  <div class="field" style="top:257px;height:20px;color:var(--ink);padding:5px 8px;border-radius:4px 4px 0 0">MP3 Audio
    <svg viewBox="0 0 8 8" style="position:absolute;right:6px;top:7px;width:6px;height:6px;fill:none;stroke:#1d1d1d;stroke-width:1.2"><path d="M1 2.5l3 3 3-3"/></svg></div>
  <div class="field" style="top:276px;height:20px;border-radius:0;padding:5px 8px">Text-to-Speech</div>
  <div class="field" style="top:295px;height:20px;border-radius:0 0 4px 4px;padding:5px 8px">Audio Recording</div>
  <div class="label" style="top:335px">Choose audio from files</div>
  <svg viewBox="0 0 10 10" style="left:175px;top:334px;width:9px;height:9px;fill:none;stroke:#1d1d1d;stroke-width:1.1"><path d="M2 4v5h6V4M5 1v5M3 3l2-2 2 2"/></svg>
  <div class="field" style="top:349px;height:21px;padding:6px 5px">MP3 Audio</div>
  <div class="btn-add">Add</div>
</section>

<!-- Screen 3: Devices available -->
<section class="screen s3">
  <div class="brand-name">Varelko</div>
  <div class="top-icons">
    <svg viewBox="0 0 12 12"><path d="M1 5a7 7 0 0 1 10 0M3 7a4 4 0 0 1 6 0"/><circle cx="6" cy="9.5" r=".8" fill="#1d1d1d"/></svg>
    <svg viewBox="0 0 12 12"><rect x="1" y="1" width="4" height="4"/><rect x="7" y="1" width="4" height="4"/><rect x="1" y="7" width="4" height="4"/><rect x="7" y="7" width="4" height="4"/></svg>
    <svg viewBox="0 0 12 12"><circle cx="6" cy="6" r="5"/><circle cx="6" cy="5" r="1.8"/><path d="M3 9.5a4 3 0 0 1 6 0"/></svg>
  </div>
  <div class="title" style="top:84px">Devices Available to connect</div>
  <div class="illustration" role="img" aria-label="Illustration of a Wi-Fi siren device on a yellow brand circle"></div>
  <div class="device" style="top:233px">Xyz timer <span class="toggle" style="position:relative"></span></div>
  <div class="device" style="top:263px">IT Siren abc <span class="toggle off" style="position:relative"></span></div>
  <div class="device" style="top:293px">Support team speaker <span class="toggle off" style="position:relative"></span></div>
</section>

<!-- Screen 4: Wi-Fi pairing -->
<section class="screen s4">
  <div class="brand-name">Varelko</div>
  <div class="top-icons">
    <svg viewBox="0 0 12 12"><path d="M1 5a7 7 0 0 1 10 0M3 7a4 4 0 0 1 6 0"/><circle cx="6" cy="9.5" r=".8" fill="#1d1d1d"/></svg>
    <svg viewBox="0 0 12 12"><rect x="1" y="1" width="4" height="4"/><rect x="7" y="1" width="4" height="4"/><rect x="1" y="7" width="4" height="4"/><rect x="7" y="7" width="4" height="4"/></svg>
    <svg viewBox="0 0 12 12"><circle cx="6" cy="6" r="5"/><circle cx="6" cy="5" r="1.8"/><path d="M3 9.5a4 3 0 0 1 6 0"/></svg>
  </div>
  <div class="title" style="top:83px;line-height:14px;font-size:9.5px">you will be connecting to Xyz timer to<br>your account using wi-fi pairing</div>
  <div class="pair-mark">Varelko</div>
  <div class="pair">
    <svg viewBox="0 0 32 32" style="left:7px;top:5px;width:29px;height:29px;fill:none;stroke:#1d1d1d;stroke-width:2"><circle cx="16" cy="16" r="14"/><circle cx="16" cy="12" r="5"/><path d="M7 26a10 8 0 0 1 18 0"/></svg>
    <svg viewBox="0 0 120 2" style="left:42px;top:19px;width:92px;height:2px"><line x1="0" y1="1" x2="120" y2="1" stroke="#c9c9c9" stroke-dasharray="3 2"/></svg>
    <svg viewBox="0 0 32 32" style="left:137px;top:4px;width:30px;height:30px;fill:none;stroke:#1d1d1d;stroke-width:2.2"><circle cx="16" cy="18" r="11"/><path d="M16 11v7l4 3M13 3h6M16 3v4M26 8l2-2"/></svg>
  </div>
  <div style="left:24px;top:322px;font-size:11px;font-weight:500">abc</div>
  <div style="left:142px;top:322px;font-size:11px;font-weight:500">Xyz timer</div>
</section>

</div>
</body>
</html>
```